strength and conditioning business focused on helping people move more efficiently

I need a business card designed for a Philadelphia based company called Brsk Lft Motion (pronounced Brisk Lift). We offer fitness professional services with the idea of helping people feel better and move optimally. We do this by designing and walking through individualized programs as well as minor soft tissue work. Our perfect client would be athletes but we will be marketing to parents who have children that are active They remember their former athletic days and want to get as close as possible back to that feeling. Attached will be the official logo and logo formats. I would love for the design to communicate trustworthy and creative. I would also love for the design to be square with rounded edges.

Target Market(s)

Parents of athletic children
former athletes
athletes

Industry/Entity Type

Fitness

Contact Information for Business Card

Business: Brsk Lft Performance
Name: Coach Calvin Ashworth
Position: Strength and Conditioning Coach / Certified Personal Trainer
Contact: coach.ash@brsklft.com
Text: (555)204-7781

Font styles to use
Serif
Sans Serif

Colors
fbee38
fbee3e
0255a3
3176b5
ffffff

Requirements
Must have
• use of logo
Nice to have
• Square design
rounded edges

```html
<!DOCTYPE html>
<html lang="en">
<head>
<meta charset="utf-8">
<title>Brsk Lft Motion – Business Card</title>
<link rel="stylesheet" href="https://fonts.googleapis.com/css2?family=Arimo:wght@400;700&display=swap">
<style>
  :root {
    --navy: #0a3184;
    --card-blue: #0b2f80;
    --accent-yellow: #fbd92e;
    --paper: #ffffff;
    --ink-grey: #3a3a3a;
    --backdrop: #2b2b2b;
  }
  * { box-sizing: border-box; margin: 0; padding: 0; }
  html, body {
    width: 1200px; height: 859px; overflow: hidden;
    background: var(--backdrop);
    font-family: "Arimo", Arial, sans-serif;
  }
  .stage { position: relative; width: 1200px; height: 859px; }
  .card {
    position: absolute; top: 208px;
    width: 446px; height: 446px;
    border-radius: 30px;
    overflow: hidden;
  }
  .card--front { left: 142px; background: var(--paper); }
  .card--back  { left: 626px; background: var(--card-blue); }

  .brand {
    position: absolute; left: 0; right: 0;
    display: flex; align-items: center; justify-content: center; gap: 12px;
    font-weight: 700; font-size: 38px; letter-spacing: 0.5px; white-space: nowrap;
  }
  .brand__dot {
    width: 40px; height: 40px; border-radius: 50%;
    background: var(--accent-yellow); flex: none;
  }
  .card--front .brand { top: 90px; color: var(--navy); }
  .card--back .brand  { top: 200px; color: var(--paper); }

  .contact { position: absolute; left: 0; right: 0; top: 220px; text-align: center; }
  .contact__name {
    color: var(--navy); font-weight: 700; font-size: 22px; letter-spacing: 0.3px;
  }
  .contact__role {
    margin-top: 6px; color: var(--ink-grey); font-size: 15.5px; line-height: 20px;
  }
  .contact__rule {
    width: 22px; height: 2px; background: var(--accent-yellow);
    margin: 10px auto 8px;
  }
  .contact__icons { display: block; margin: 0 auto 4px; }
  .contact__line { color: var(--ink-grey); font-size: 16.5px; line-height: 21.5px; }
</style>
</head>
<body>
<main class="stage">
  <section class="card card--front" aria-label="Business card front">
    <div class="brand"><span class="brand__dot"></span>Brsk Lft Motion</div>
    <div class="contact">
      <p class="contact__name">COACH CALVIN ASHWORTH</p>
      <p class="contact__role">Strength and Conditioning Coach /<br>Certified Personal Trainer</p>
      <div class="contact__rule"></div>
      <svg class="contact__icons" width="60" height="14" viewBox="0 0 60 14" aria-hidden="true">
        <path d="M2 3 C2 2 3 1 4 1 L5.5 1 L6.5 4 L5 5 C5.8 7 7 8.2 9 9 L10 7.5 L13 8.5 L13 10 C13 11 12 12 11 12 C6 12 2 8 2 3 Z" fill="var(--navy)"/>
        <line x1="15" y1="7" x2="20" y2="7" stroke="var(--accent-yellow)" stroke-width="1.5"/>
        <rect x="22" y="2.5" width="14" height="9" fill="var(--navy)"/>
        <path d="M22.5 3 L29 8 L35.5 3" fill="none" stroke="var(--paper)" stroke-width="1.2"/>
        <line x1="38" y1="7" x2="43" y2="7" stroke="var(--accent-yellow)" stroke-width="1.5"/>
        <circle cx="51" cy="7" r="5.6" fill="var(--navy)"/>
        <path d="M45.4 7 H56.6 M51 1.4 V12.6 M51 1.4 C48 4 48 10 51 12.6 M51 1.4 C54 4 54 10 51 12.6" fill="none" stroke="var(--paper)" stroke-width="0.8"/>
      </svg>
      <p class="contact__line">(555)204-7781</p>
      <p class="contact__line">coach.ash@brsklft.com</p>
      <p class="contact__line">www.brsklft.com</p>
    </div>
  </section>

  <section class="card card--back" aria-label="Business card back">
    <div class="brand"><span class="brand__dot"></span>Brsk Lft Motion</div>
  </section>
</main>
</body>
</html>
```